Stationary (Business Cards, envelopes, cover letters, etc) for HARBOR LANTERN ALLIANCE
The Harbor Lantern Alliance
Stationary (Business Cards, envelopes, cover letters, etc) for HARBOR LANTERN ALLIANCE - Business Opportunities
Creative Brief
Professional
Rodrigo Vallejo Pemberton
Av. Ernesto Palafox 728 B Col. Las Cumbres Olmeda México DF CP 04821 México
rvallejo@hla-ejemplo.mx
www.hla-ejemplo.mx
First impressions have high impact, so in terms of the business card, it has to be something that's out of the box. The card is used to present ourselves to another party or prospect, but it also has to have a high impact message, either by an image or a phrase that comes attached in the back side. It could be some key points of a preview success case. So the back side has to have a marketing application. It has to be a card that will stand out, so much that it will be shown and passed around. In design and in materials (maybe???), although win the materials it will have a high impact on the costs of production. It has to be standard size, so it fits in every wallet thus avoiding on being thrown somewhere.
Concepts
Business Card and Stationary Project for a multifaceted corporation
Stationary for holding company
Business cards for RFKO - Investimentos e Holdings
mitiha mitiha
GREAT NEWS! WE'VE EXTENDED TO THIS FRIDAY! KEEP UP THE GREAT WORK!!!
Hi designers! GREAT JOB! We are want to decide today (our time) the winner. Please if you have any questions, let us know. Try to show as much applications as possible, i.e. we're now in a digital world so some digital applications we'll be considered for higher points. Have seen proposals in blue and gray (predominant colors and mixed), but none in orange. Let's see some! *Don't use curved lines in your design proposals. THANKS!
Hi, first of all I want to thank each and every one of you for accepting in working on our project. GREAT DESIGNS !!!!! Something we don't want is the lines that make a "curve" to separate content. I've seen a lot of those in the market and we want to be ORIGINAL. As I said in the brief, we want our cards to be saved as something awsome, and to be shown to other people. Material: sent your proposals of other materials, however if you can also send the specificatiosn of that material so we can see the cost of printing in them. Remember that it's not only the business cards but the stationary. KEEP UP THE GREAT JOB! CREATE DESIGN!

```html
<!DOCTYPE html>
<html lang="es">
<head>
<meta charset="utf-8">
<title>Harbor Lantern Alliance — Stationery</title>
<link href="https://fonts.googleapis.com/css2?family=Montserrat:wght@400;600;800&display=swap" rel="stylesheet">
<style>
  :root{
    --ink:#1b1b1b;
    --paper:#ffffff;
    --backdrop:#ecebe7;
    --orange:#f0892a;
    --blue:#2f8fd6;
    --grey:#8d8f92;
    --faint:#e6ecf3;
    --rule:#c9c9c9;
    --text:#3a3a3a;
  }
  *{box-sizing:border-box;margin:0;padding:0}
  html,body{width:1200px;height:437px;overflow:hidden}
  body{background:var(--backdrop);font-family:"Montserrat",Arial,sans-serif;color:var(--text);position:relative}
  .item{position:absolute;background:var(--paper);box-shadow:0 1px 3px rgba(0,0,0,.25)}
  .brand{font-weight:800;letter-spacing:.04em;line-height:1.05;display:flex;align-items:center;gap:4px;color:var(--ink)}
  .brand .mark{display:inline-block;background:var(--orange);flex:none}
  .brand.light{color:#fff}
  .faint-name{position:absolute;font-weight:800;color:var(--faint);line-height:1;letter-spacing:.02em}

  /* folder */
  .folder{left:10px;top:6px;width:200px;height:425px;background:transparent;box-shadow:none}
  .folder-cover{position:absolute;left:0;top:0;width:200px;height:292px;display:flex;box-shadow:0 1px 3px rgba(0,0,0,.25)}
  .folder-back{width:100px;background:var(--ink);position:relative}
  .folder-front{width:100px;background:var(--paper);position:relative;overflow:hidden}
  .folder-back .brand{position:absolute;left:12px;top:22px;font-size:6px}
  .folder-back .big-name{position:absolute;left:12px;top:150px;color:#fff;font-weight:800;font-size:17px;line-height:1.05}
  .folder-pocket{position:absolute;left:0;top:292px;width:200px;height:133px}
  .folder-pocket .card-slot{position:absolute;left:116px;top:80px;width:60px;height:34px;background:#fafafa;border:1px solid var(--rule);font-size:3.5px;padding:12px 4px}

  /* disc */
  .disc{left:224px;top:18px;width:58px;height:58px;border-radius:50%;display:flex;align-items:center;justify-content:center}
  .disc::after{content:"";position:absolute;width:12px;height:12px;border-radius:50%;background:var(--backdrop);border:3px solid #ddd}

  /* letterheads */
  .letterhead{width:125px;height:162px;padding:10px 9px}
  .letterhead .brand{font-size:4.6px}
  .letterhead .brand .mark{width:7px;height:7px}
  .letter-lines{position:absolute;left:9px;right:9px;top:40px}
  .letter-lines span{display:block;height:1px;background:var(--rule);margin-bottom:6px}
  .letter-foot{position:absolute;left:9px;right:9px;bottom:8px;font-size:3px;line-height:1.4;color:var(--grey)}
  .letter-foot::before{content:"";display:block;height:2px;background:linear-gradient(90deg,var(--orange) 33%,var(--blue) 33% 66%,var(--grey) 66%);margin-bottom:3px}
  .doc-table{position:absolute;left:9px;right:9px;top:36px;border-collapse:collapse;width:107px;font-size:4px}
  .doc-table td{border:1px solid var(--rule);height:11px;padding:0 3px}

  /* cards */
  .card{width:68px;height:40px;padding:6px}
  .card.dark{background:var(--ink)}
  .card .brand{font-size:3.8px}
  .card .brand .mark{width:6px;height:6px}
  .card-contact{position:absolute;left:6px;bottom:5px;font-size:2.6px;line-height:1.45;color:var(--text)}
  .card-contact strong{font-weight:600;font-size:3.2px;color:var(--ink)}

  /* envelope */
  .envelope{left:672px;top:330px;width:190px;height:92px}
  .envelope svg{position:absolute;left:0;top:0}
  .envelope .brand{position:absolute;left:72px;top:10px;font-size:4.5px}

  /* devices screens */
  .phone-screen{left:1124px;top:120px;width:44px;height:84px;border-radius:3px;display:flex;align-items:center;justify-content:center}
  .tablet-screen{left:1046px;top:255px;width:136px;height:172px;background:var(--ink);border-radius:4px;display:flex;align-items:center;justify-content:center}
</style>
</head>
<body>

<!-- presentation folder -->
<section class="item folder" aria-label="Presentation folder">
  <div class="folder-cover">
    <div class="folder-back">
      <div class="brand light"><span class="mark" style="width:8px;height:8px"></span>HARBOR LANTERN<br>ALLIANCE</div>
      <div class="big-name">HARBOR<br>LANTERN<br>ALLIANCE</div>
    </div>
    <div class="folder-front">
      <div class="faint-name" style="left:8px;top:120px;font-size:22px">HARBOR<br>LANTERN<br>ALLIANCE</div>
    </div>
  </div>
  <svg class="folder-pocket" width="200" height="133" viewBox="0 0 200 133">
    <polygon points="0,0 100,0 100,12 88,24 12,24 0,12" fill="#ffffff" stroke="#d0d0d0"/>
    <polygon points="100,0 200,0 200,12 188,24 112,24 100,12" fill="#ffffff" stroke="#d0d0d0"/>
    <polygon points="4,24 96,24 96,118 86,130 14,130 4,118" fill="#ffffff" stroke="#d0d0d0"/>
    <polygon points="104,24 196,24 196,118 186,130 114,130 104,118" fill="#ffffff" stroke="#d0d0d0"/>
  </svg>
  <div class="card-slot" style="position:absolute;left:116px;top:372px;width:62px;height:34px;background:#fafafa;border:1px solid var(--rule);font-size:3.5px;font-weight:800;padding:14px 4px;color:var(--ink)">HARBOR LANTERN ALLIANCE</div>
</section>

<!-- disc -->
<div class="item disc"><span class="brand" style="position:absolute;top:9px;font-size:3px">HARBOR LANTERN ALLIANCE</span></div>

<!-- small envelope & card, top row -->
<div class="item card" style="left:292px;top:12px;width:60px;height:34px"><div class="brand"><span class="mark"></span>HARBOR LANTERN<br>ALLIANCE</div></div>
<div class="item card" style="left:292px;top:52px;width:60px;height:22px"></div>

<!-- letterhead with table -->
<article class="item letterhead" style="left:225px;top:84px">
  <div class="brand"><span class="mark"></span>HARBOR LANTERN<br>ALLIANCE</div>
  <table class="doc-table">
    <tr><td>Fecha</td><td></td></tr>
    <tr><td>Cliente</td><td></td></tr>
    <tr><td>Asunto</td><td></td></tr>
    <tr><td>Notas</td><td></td></tr>
    <tr><td></td><td></td></tr>
  </table>
  <div class="letter-foot">Av. Ernesto Palafox 728 B Col. Las Cumbres Olmeda México DF CP 04821 México</div>
</article>

<!-- letterhead with faint name -->
<article class="item letterhead" style="left:225px;top:258px;height:168px;overflow:hidden">
  <div class="faint-name" style="left:12px;top:60px;font-size:20px">HARBOR<br>LANTERN<br>ALLIANCE</div>
</article>

<!-- letterhead standard -->
<article class="item letterhead" style="left:365px;top:84px">
  <div class="brand"><span class="mark"></span>HARBOR LANTERN<br>ALLIANCE</div>
  <div class="letter-lines"><span></span><span></span><span></span><span></span><span></span><span></span><span></span><span></span><span></span><span></span></div>
  <div class="letter-foot">www.hla-ejemplo.mx · rvallejo@hla-ejemplo.mx</div>
</article>

<article class="item letterhead" style="left:365px;top:258px;height:168px;overflow:hidden">
  <div class="brand"><span class="mark"></span>HARBOR LANTERN<br>ALLIANCE</div>
  <div class="faint-name" style="left:12px;top:70px;font-size:20px">HARBOR<br>LANTERN<br>ALLIANCE</div>
</article>

<article class="item letterhead" style="left:510px;top:84px">
  <div class="brand"><span class="mark"></span>HARBOR LANTERN<br>ALLIANCE</div>
  <div class="letter-lines"><span></span><span></span><span></span><span></span><span></span><span></span><span></span><span></span></div>
  <div class="letter-foot">Av. Ernesto Palafox 728 B Col. Las Cumbres Olmeda México DF CP 04821 México</div>
</article>

<article class="item letterhead" style="left:510px;top:258px;height:168px;overflow:hidden">
  <div class="faint-name" style="left:12px;top:60px;font-size:20px">HARBOR<br>LANTERN<br>ALLIANCE</div>
</article>

<!-- compliment slips -->
<article class="item letterhead" style="left:672px;top:84px;height:110px">
  <div class="brand"><span class="mark"></span>HARBOR LANTERN<br>ALLIANCE</div>
  <div class="letter-foot">www.hla-ejemplo.mx</div>
</article>
<article class="item letterhead" style="left:672px;top:205px;height:110px">
  <div class="letter-lines" style="top:14px"><span></span><span></span><span></span><span></span><span></span><span></span></div>
</article>

<!-- envelope -->
<div class="item envelope">
  <svg width="190" height="92" viewBox="0 0 190 92">
    <polygon points="0,0 190,0 95,46" fill="#1b1b1b"/>
    <line x1="0" y1="92" x2="95" y2="46" stroke="#d4d4d4"/>
    <line x1="190" y1="92" x2="95" y2="46" stroke="#d4d4d4"/>
  </svg>
  <div class="brand light" style="position:absolute;left:62px;top:10px;font-size:4.5px"><span class="mark" style="width:7px;height:7px"></span>HARBOR LANTERN<br>ALLIANCE</div>
</div>

<!-- business cards -->
<div class="item card" style="left:510px;top:10px"><div class="brand"><span class="mark"></span>HARBOR LANTERN<br>ALLIANCE</div></div>
<div class="item card dark" style="left:584px;top:10px"><div class="brand light"><span class="mark"></span>HARBOR LANTERN<br>ALLIANCE</div></div>
<div class="item card" style="left:700px;top:10px">
  <div class="brand"><span class="mark"></span>HARBOR LANTERN<br>ALLIANCE</div>
</div>
<div class="item card" style="left:774px;top:10px">
  <div class="card-contact"><strong>Rodrigo Vallejo Pemberton</strong><br>Director General<br>rvallejo@hla-ejemplo.mx<br>www.hla-ejemplo.mx</div>
</div>
<div class="item card" style="left:860px;top:10px"><div class="brand"><span class="mark"></span>HARBOR LANTERN<br>ALLIANCE</div></div>
<div class="item card" style="left:934px;top:10px">
  <div class="card-contact"><strong>Rodrigo Vallejo Pemberton</strong><br>rvallejo@hla-ejemplo.mx<br>www.hla-ejemplo.mx</div>
</div>
<div class="item card dark" style="left:1010px;top:10px"><div class="brand light"><span class="mark"></span>HARBOR LANTERN<br>ALLIANCE</div></div>
<div class="item card" style="left:860px;top:58px"></div>
<div class="item card" style="left:934px;top:58px"></div>

<!-- letterhead far right -->
<article class="item letterhead" style="left:860px;top:120px;height:190px">
  <div class="brand"><span class="mark"></span>HARBOR LANTERN<br>ALLIANCE</div>
  <div class="letter-lines"><span></span><span></span><span></span><span></span><span></span><span></span><span></span><span></span><span></span><span></span><span></span><span></span></div>
  <div class="letter-foot">www.hla-ejemplo.mx · rvallejo@hla-ejemplo.mx</div>
</article>

<!-- phone screen -->
<div class="item phone-screen"><div class="brand" style="font-size:4px;flex-direction:column"><span class="mark" style="width:8px;height:8px"></span>HARBOR LANTERN ALLIANCE</div></div>

<!-- tablet screen -->
<div class="item tablet-screen"><div class="brand light" style="font-size:11px;flex-direction:column;text-align:center;gap:8px"><span class="mark" style="width:18px;height:18px"></span>HARBOR<br>LANTERN<br>ALLIANCE</div></div>

</body>
</html>
```